R. Talmont Realty, Inc business card (2 sided), letterhead (1 sided) & #10 envelope (1 sided)

business card of standard size utilizing the attached logo. Side one with logo, Owen Talmont (my name), President / Broker (title), 805-317-2684 (phone), www.rtalmontrealty.example (website), 1726 Harlow Avenue, Suite 4052 San Luis Obiso, CA 93628 (business address) owen.rtalmontrealty@mailbox.example (e-mail address),
Side two - Log

Letterhead and #10 envelope in the same theme
Updates

Project Deadline Extended
Reason: I think a 2 day deadline may be a bit ambitious on my part. I have extended the deadline to 4 days. Thanks!

Industry/Entity Type

Business

```html
<!DOCTYPE html>
<html lang="en">
<head>
<meta charset="utf-8">
<title>R. Talmont Realty, Inc — Business Card</title>
<link rel="stylesheet" href="https://fonts.googleapis.com/css2?family=Noto+Serif:wght@400;700&family=Open+Sans:wght@400;600&display=swap">
<style>
  :root {
    --stage: #e8e5e0;
    --paper: #ffffff;
    --brand-blue: #1c6e97;
    --brand-blue-deep: #0d4e70;
    --brand-blue-light: #2a8fc0;
    --ink: #2b2b2b;
    --ink-soft: #3a3a3a;
    --rule: #9a9a9a;
    --band-dark: #2e2e30;
  }
  * { box-sizing: border-box; margin: 0; padding: 0; }
  html, body {
    width: 1200px; height: 1182px; overflow: hidden;
    background: var(--stage);
  }
  .canvas { position: relative; width: 1200px; height: 1182px; }

  .card {
    position: absolute;
    width: 911px; height: 520px;
    box-shadow: 0 4px 14px rgba(0,0,0,0.18);
    overflow: hidden;
  }
  .card--front { left: 35px; top: 44px; background: var(--paper); }
  .card--back {
    left: 246px; top: 629px;
    background: radial-gradient(ellipse at 50% 40%, var(--brand-blue-light) 0%, var(--brand-blue) 45%, var(--brand-blue-deep) 100%);
  }

  .wordmark {
    position: absolute; left: 0; right: 0;
    display: flex; align-items: center; justify-content: center; gap: 16px;
    font-family: "Noto Serif", Georgia, serif;
    font-weight: 400;
    font-size: 46px;
    letter-spacing: 0.5px;
  }
  .wordmark__mark { width: 26px; height: 26px; }
  .card--front .wordmark { top: 118px; color: var(--brand-blue); }
  .card--front .wordmark__mark { background: var(--brand-blue); }
  .card--back .wordmark { top: 218px; color: #ffffff; }
  .card--back .wordmark__mark { background: #ffffff; }

  .person {
    position: absolute; right: calc(911px - 382px); top: 358px;
    text-align: right;
    font-family: "Noto Serif", Georgia, serif;
  }
  .person__name { font-weight: 700; font-size: 30px; color: var(--brand-blue); line-height: 1.2; }
  .person__title { font-weight: 400; font-size: 25px; color: var(--ink); margin-top: 8px; }

  .divider {
    position: absolute; left: 403px; top: 335px;
    width: 1px; height: 158px; background: var(--rule);
  }

  .contact {
    position: absolute; left: 423px; top: 336px;
    list-style: none;
    font-family: "Open Sans", Arial, sans-serif;
    font-size: 21px; color: var(--ink-soft);
  }
  .contact__item { display: flex; align-items: center; gap: 8px; height: 40px; }
  .contact__icon { width: 18px; height: 18px; flex: none; }

  .band { position: absolute; left: 0; bottom: 0; width: 911px; height: 26px; }

  .site {
    position: absolute; left: 0; right: 0; top: 426px;
    text-align: center;
    font-family: "Open Sans", Arial, sans-serif;
    font-weight: 600; font-size: 28px; letter-spacing: 4px;
    color: #ffffff;
  }
</style>
</head>
<body>
<main class="canvas">

  <section class="card card--front" aria-label="Business card, front">
    <div class="wordmark"><span class="wordmark__mark"></span><span>R. Talmont Realty, Inc</span></div>

    <div class="person">
      <p class="person__name">Owen Talmont</p>
      <p class="person__title">President / Broker</p>
    </div>

    <div class="divider"></div>

    <ul class="contact">
      <li class="contact__item">
        <svg class="contact__icon" viewBox="0 0 18 18" aria-hidden="true">
          <circle cx="9" cy="9" r="8" fill="none" stroke="#1c6e97" stroke-width="1.5"/>
          <path d="M6 5 l2 0 l0.8 2.4 l-1.2 1 a5 5 0 0 0 2 2 l1 -1.2 l2.4 0.8 l0 2 a1 1 0 0 1 -1 1 a7 7 0 0 1 -7 -7 a1 1 0 0 1 1 -1z" fill="#1c6e97"/>
        </svg>
        <span>805-317-2684</span>
      </li>
      <li class="contact__item">
        <svg class="contact__icon" viewBox="0 0 18 18" aria-hidden="true">
          <rect x="2" y="5" width="14" height="9" rx="1" fill="#1c6e97"/>
          <path d="M2.5 5.5 L9 10 L15.5 5.5" fill="none" stroke="#fff" stroke-width="1.2"/>
        </svg>
        <span>owen.rtalmontrealty@mailbox.example</span>
      </li>
      <li class="contact__item">
        <svg class="contact__icon" viewBox="0 0 18 18" aria-hidden="true">
          <circle cx="9" cy="9" r="7.5" fill="#1c6e97"/>
          <g fill="none" stroke="#fff" stroke-width="1">
            <ellipse cx="9" cy="9" rx="3" ry="7.5"/>
            <line x1="1.5" y1="9" x2="16.5" y2="9"/>
            <line x1="9" y1="1.5" x2="9" y2="16.5"/>
          </g>
        </svg>
        <span>www.rtalmontrealty.example</span>
      </li>
    </ul>

    <svg class="band" viewBox="0 0 911 26" preserveAspectRatio="none" aria-hidden="true">
      <rect x="0" y="8" width="911" height="18" fill="var(--band-dark)"/>
      <polygon points="360,26 400,0 911,0 911,26" fill="var(--brand-blue)"/>
      <polygon points="378,26 394,14 911,14 911,26" fill="var(--brand-blue-deep)"/>
    </svg>
  </section>

  <section class="card card--back" aria-label="Business card, back">
    <div class="wordmark"><span class="wordmark__mark"></span><span>R. Talmont Realty, Inc</span></div>
    <p class="site">www.rtalmontrealty.example</p>
  </section>

</main>
</body>
</html>
```